Veltrane Group Business Card Design

The CEO is looking for a new trendy look for his business card.
You can stay with current branding or come up with something new/creative. It can be 3D, including Medical Office buildings. You can use our logo in a variety of colors. Please include name, title, company name, company website, email address, cell number

Target Market(s)

Real Estate Development and Construction

Industry/Entity Type

Health care real estate

Contact Information for Business Card

Rohesh Kamdar, CEO M-604.781.2249 E-roheshkamdar@veltrane.com Address:4180 Lindqvist Ave, Tampa, FL 33482 www.veltrane.com

Font styles to use
Other font styles liked:
• Be creative

Requirements
Must have
• Creative, trendy look
Nice to have
• Please go to our website to get a feel- www. veltrane.com
Should not have
• small fonts

```html
<!DOCTYPE html>
<html lang="en">
<head>
<meta charset="UTF-8">
<title>Veltrane Group Business Card</title>
<link href="https://fonts.googleapis.com/css2?family=Lato:wght@400;700;900&display=swap" rel="stylesheet">
<style>
  :root {
    --brand-red: #b01f2b;
    --ink: #1a1a1a;
    --paper: #ffffff;
    --backdrop: #3a3a3a;
    --rule: #222222;
  }
  * { margin: 0; padding: 0; box-sizing: border-box; }
  html, body {
    width: 1200px;
    height: 694px;
    overflow: hidden;
    background: var(--backdrop);
    font-family: 'Lato', Arial, sans-serif;
  }
  .canvas {
    width: 1200px;
    height: 694px;
    display: flex;
    align-items: center;
    justify-content: center;
    gap: 50px;
  }
  .card {
    width: 520px;
    height: 300px;
    border-radius: 26px;
    position: relative;
    overflow: hidden;
  }
  .card--front {
    background: var(--brand-red);
    display: flex;
    align-items: center;
    justify-content: center;
  }
  .wordmark {
    font-weight: 900;
    letter-spacing: -1px;
    line-height: 1;
  }
  .card--front .wordmark {
    color: var(--paper);
    font-size: 58px;
  }
  .card--back {
    background: var(--paper);
    color: var(--ink);
  }
  .card--back .wordmark {
    position: absolute;
    top: 40px;
    right: 40px;
    color: var(--brand-red);
    font-size: 38px;
  }
  .holder {
    position: absolute;
    left: 40px;
    top: 140px;
  }
  .holder__name {
    color: var(--brand-red);
    font-weight: 700;
    font-size: 28px;
    line-height: 1.1;
  }
  .holder__title {
    font-size: 16px;
    margin-top: 4px;
  }
  .address {
    position: absolute;
    right: 40px;
    top: 142px;
    text-align: right;
    font-size: 16px;
    line-height: 1.35;
  }
  .divider {
    position: absolute;
    left: 40px;
    right: 40px;
    top: 204px;
    height: 1.5px;
    background: var(--rule);
  }
  .contacts {
    position: absolute;
    left: 40px;
    top: 216px;
    list-style: none;
    font-size: 16px;
    line-height: 24px;
  }
  .contacts li {
    display: flex;
    align-items: center;
    gap: 10px;
  }
  .contacts svg {
    width: 16px;
    height: 16px;
    flex: none;
  }
</style>
</head>
<body>
<main class="canvas">
  <section class="card card--front" aria-label="Card front">
    <div class="wordmark">Veltrane Group</div>
  </section>

  <section class="card card--back" aria-label="Card back">
    <div class="wordmark">Veltrane Group</div>

    <div class="holder">
      <div class="holder__name">Rohesh Kamdar</div>
      <div class="holder__title">CEO</div>
    </div>

    <address class="address" style="font-style: normal;">
      4180 Lindqvist Ave, Tampa,<br>FL 33482
    </address>

    <div class="divider"></div>

    <ul class="contacts">
      <li>
        <svg viewBox="0 0 16 16" aria-hidden="true">
          <rect x="4" y="1" width="8" height="14" rx="1.5" fill="none" stroke="#b01f2b" stroke-width="1.6"/>
          <circle cx="8" cy="12.3" r="0.9" fill="#b01f2b"/>
        </svg>
        604.781.2249
      </li>
      <li>
        <svg viewBox="0 0 16 16" aria-hidden="true">
          <rect x="1" y="3" width="14" height="10" rx="1" fill="#b01f2b"/>
          <path d="M1.5 3.8 L8 9 L14.5 3.8" fill="none" stroke="#ffffff" stroke-width="1.3"/>
        </svg>
        roheshkamdar@veltrane.com
      </li>
      <li>
        <svg viewBox="0 0 16 16" aria-hidden="true">
          <circle cx="8" cy="8" r="7" fill="#b01f2b"/>
          <ellipse cx="8" cy="8" rx="3" ry="7" fill="none" stroke="#ffffff" stroke-width="1"/>
          <line x1="1" y1="8" x2="15" y2="8" stroke="#ffffff" stroke-width="1"/>
        </svg>
        www.veltrane.com
      </li>
    </ul>
  </section>
</main>
</body>
</html>
```